Sustainably Transforming Education

Company is education services based. early learning through adult and corporate. Focus is national government policy and program design and delivery alongside a research based and academically grounded set of approaches to planning, evaluation, and change management.I am looking for an innovative design position that aligns with the global agendas for innovation, creativity and collaboration at international and national policy levels (berulo is a name that reflects these qualities - colours need to reflect amythyst in some way). I also need a design that translates from a business card as 1 medium of interaction to a template that can work in word/powerpoint etc to support both stationery as well as a digital strategy across multiple channels (fb/twit/etc)There is no slogan/tag line for the company and their is no logo. I was looking to just leverage the name - have currently played around with various fonts (ending up with cuisine - all lowercase).

Industry/Entity Type

Adult

Contact Information for Business Card

name: berulo (all lowercase)Chairman: Andrew CrowMobile: +61 418 902 131Web: www.berulo.comemail: martin.pelly@berulo-example.com

Font styles to use
Script
Other font styles liked:
• cuisine

Colors
e34298
e667a6
33a6d7
aaaaaa

Requirements
Nice to have
• https://files.example-share.net/sh/qx7kw2hd91lzmnp/AAFr3tYbQeLp8VwZnKcDs2Hu?dl=0
• Link to the printwell templates used to begin this process....the one with the lines was about people intersecting (collaborating).....the organic shapes one more of a fluid feel of people coming together - the overall shape being largely spherical could represent a "global" feel.....anyway that is how I was thinking about these

```html
<!DOCTYPE html>
<html lang="en">
<head>
<meta charset="utf-8">
<title>berulo</title>
<link rel="stylesheet" href="https://fonts.googleapis.com/css2?family=Nunito:wght@600&display=swap">
<style>
  :root {
    --amethyst-light: #e667a6;
    --amethyst: #e34298;
    --amethyst-deep: #cf3b8c;
    --white: #ffffff;
  }
  html, body {
    margin: 0;
    padding: 0;
    overflow: hidden;
    background: var(--amethyst-light);
  }
  .card {
    position: relative;
    width: 1200px;
    height: 740px;
    overflow: hidden;
    background: var(--amethyst-light);
  }
  .card__shapes {
    position: absolute;
    inset: 0;
    width: 1200px;
    height: 740px;
  }
  .shape--organic { fill: var(--amethyst); }
  .world-map-area {
    position: absolute;
    left: 270px;
    top: 138px;
    width: 740px;
    height: 474px;
    border-radius: 46% 50% 44% 48%;
    background: radial-gradient(ellipse at 50% 45%, rgba(207, 59, 140, 0.75) 0%, rgba(207, 59, 140, 0.35) 60%, rgba(207, 59, 140, 0) 100%);
  }
  .company-name {
    position: absolute;
    left: 0;
    top: 312px;
    width: 1200px;
    height: 120px;
    margin: 0;
    padding-left: 84px;
    box-sizing: border-box;
    text-align: center;
    font-family: "Nunito", sans-serif;
    font-weight: 600;
    font-size: 100px;
    line-height: 120px;
    letter-spacing: 1px;
    color: var(--white);
  }
</style>
</head>
<body>
  <main class="card">
    <svg class="card__shapes" viewBox="0 0 1200 740" aria-hidden="true">
      <path class="shape--organic" d="M0,0 H470 C640,20 880,40 1010,105 L1074,162 C1050,152 1035,148 1025,150 C1090,300 1130,560 1150,740 H470 C320,560 120,370 0,150 Z"/>
    </svg>
    <div class="world-map-area" role="img" aria-label="Faint world map silhouette in deep amethyst pink"></div>
    <h1 class="company-name">berulo</h1>
  </main>
</body>
</html>
```